Bold, Modern, Clean "Kestrelwaymassage.com" website

Why we stand out?
We are a male and female mobile massage team. Our names are Paul and Lina. 
Kestrel Way is a Seattle based mobile massage service. Our massage is offered to the community with a goal of facilitating balance within each individual. We specialize in integrated Pain management, and sports/medical massage therapy. Every client's first assessment is attended by our male and female massage therapist team. Depending on the goals identified for an individual determines which therapist will be assigned to provide treatment, if not both.

Our passion...
Here at Kestrel Way, we have a great passion for Postural Resoration and how it is integrated into an individual's Massage treatment. We pride ourselves in being natural facilitators of healing, which takes the ego of the therapist out of the client's healing process. We strive to deliver the best massage possible by including modalities such as Neuromuscular, Myofascial release, spontaneous muscle release, postural restoration, orthopedic, and medical massage.

Our education...

We are both Graduates of Venmora, school of massage therapy. We have continuing education in medical massage, myofacial release, trigger point therapy, postural restoration, anatomy, and spontaneous muscle release. Lina is also a Certified Yoga Instructor, which amplifies her experience with flexibility and strength as it pertains to each individual. Paul's passion is Massage, stretching, and strength training to encourage postural restoration and realignment.

Our rates-

Our rates are $75/ 60 minutes, $95/ 90 minutes, and $120/ 120 minutes.

Education-
Both Lina and I worked as behavioral health professionals that specialized in life skills mentoring for youth who had experienced different types of trauma. This led us both to want to help others in a different environment, where individuals can be empowered to take responsibility over their own healing. To us, massage is a type of manipulation physical therapy, that encourages healing on many levels.

Advice to any massage client-
The most important thing to 'us', as Licenced providers is to get you on to our table to show you our skills. But a good therapist never forgets that it's not about what we do for you, but what we can facilitate for you. Your health and healing has nothing to do with us. It is yours, not ours. Identify what your goals are with any Therapist, and know what the end looks like. Progress should be tangible, such as range of motion, and decreased pain.

Lina and Paul at Kestrel Way are awesome! I recently had open heart surgery, and Lina worked on me to increase my range of motion while helping with the pinched nerve from my arm being in the same position for so long during my surgery. My wife drives a lot for work, and Paul has helped decrease her neck and lower back pain immensely. They are seriously the best therapists I have ever worked with. I would recommend them to anyone who needs anything from stress relief to a medical massage treatment. They are professional, up beat, easy going, and always on time. And, I love that they meet us where ever we like! We did a staycation recently, where they came to our hotel to give us relaxation massages. Although usually they come to our home, where we focus on pain related issues. We will continue to work with them for a long, long time.

Target Market(s)

Mobile massage therapy clients

Industry/Entity Type

Massage Therapy

Coding

Coded - Design and coding required

Number of Pages Required

1 page

Font styles to use
Serif
Sans Serif

Requirements
Must have
• Please add or remove any information that would help the presentation of our website. Our logo is posted below, please include into the website.
• Please include a contact field that includes, kestrelwaymassage@fernmail.net,
• (206) 555-0148
• We have also included our own stock photos, as well as a photo of Paul and Lina. Please include a cropped photo of both massage therapists.

```html
<!DOCTYPE html>
<html lang="en">
<head>
<meta charset="utf-8">
<title>Kestrel Way – Seattle Mobile Massage</title>
<link href="https://fonts.googleapis.com/css2?family=Roboto:wght@300;400;500;700&display=swap" rel="stylesheet">
<style>
:root{
  --brand:#05a7d8;
  --brand-dark:#0894c2;
  --navy:#16305f;
  --ink:#222;
  --body:#555;
  --muted:#8a8f94;
  --pale:#eef3f6;
  --grey-band:#f0f1f2;
  --footer:#2f3030;
  --white:#fff;
  --star:#f0a030;
}
*{box-sizing:border-box;margin:0;padding:0}
html,body{width:1200px;height:2590px;overflow:hidden}
body{position:relative;background:var(--white);font-family:"Roboto",Arial,sans-serif;color:var(--ink)}
.abs{position:absolute}

/* top bar */
.top-bar{left:0;top:0;width:1200px;height:60px;background:var(--brand)}
.quick-phone{right:75px;top:17px;display:flex;align-items:center;gap:10px;color:var(--white);font-size:15px}
.quick-phone strong{font-size:18px;font-weight:500}
.quick-phone svg{width:26px;height:26px}

/* nav */
.nav-bar{left:0;top:60px;width:1200px;height:80px;background:var(--white)}
.brand-badge{left:65px;top:17px;width:112px;height:112px;border-radius:50%;background:var(--white);box-shadow:0 1px 4px rgba(0,0,0,.15);display:flex;align-items:center;justify-content:center}
.brand-name{font-size:19px;font-weight:700;color:var(--navy);text-align:center;line-height:1.1;text-transform:uppercase}
.main-nav{top:60px;left:0;width:1200px;height:80px}
.main-nav a{position:absolute;top:36px;transform:translateX(-50%);font-size:14px;color:#333;text-decoration:none;white-space:nowrap}
.main-nav a.active{color:var(--brand)}
.main-nav .active-dot{position:absolute;left:563px;top:22px;width:46px;height:46px;border-radius:50%;background:#e9f4f9}

/* hero */
.hero{left:0;top:140px;width:1200px;height:525px;background:linear-gradient(180deg,#12309a 0%,#1f49b8 55%,#2a3d7a 80%,#1b2235 100%)}
.hero-title{right:133px;top:206px;text-align:right;color:var(--white);font-size:33px;font-weight:300;line-height:44px}
.hero-arrow{top:240px;width:24px;height:30px}

/* why */
.section-title{font-size:24px;font-weight:500;color:var(--brand);text-transform:uppercase}
.why-title{left:74px;top:738px}
.why-text{left:74px;top:780px;width:586px;font-size:13.4px;line-height:21px;color:var(--body);text-align:justify}
.btn{display:flex;align-items:center;justify-content:center;background:var(--brand);color:var(--white);font-size:13px;font-weight:500;text-transform:uppercase;letter-spacing:.3px}
.learn-btn{left:74px;top:941px;width:131px;height:33px}
.why-media{left:703px;top:733px;width:423px;height:253px;background:linear-gradient(120deg,#d9d2c2 0%,#e8dccb 45%,#f1e7de 70%,#c9b7a0 100%)}
.play{left:883px;top:827px;width:64px;height:64px}

/* passion */
.passion{left:0;top:1034px;width:1200px;height:456px;background:linear-gradient(180deg,#f4f4f5,#ececed)}
.passion-title{left:0;width:1200px;top:1082px;text-align:center;font-size:24px;font-weight:400;color:#222}
.passion-text{left:74px;top:1137px;width:1052px;text-align:center;font-size:13.4px;line-height:21px;color:var(--body)}
.feature{width:320px;text-align:center}
.feature-icon{width:110px;height:110px;margin:0 auto}
.feature h3{margin-top:14px;font-size:16px;font-weight:500;color:#222;text-transform:uppercase}
.feature p{margin-top:8px;font-size:13.4px;line-height:19px;color:var(--body)}

/* pricing */
.pricing-band{left:0;top:1490px;width:1200px;height:332px;background:var(--brand)}
.pricing-base{left:0;top:1822px;width:1200px;height:242px;background:var(--pale)}
.pricing-kicker{left:0;width:1200px;top:1546px;text-align:center;color:var(--white);font-size:16px;font-weight:300;text-transform:uppercase}
.pricing-title{left:0;width:1200px;top:1567px;text-align:center;color:var(--white);font-size:30px;font-weight:300;text-transform:uppercase}
.plan{border-radius:50%;background:var(--white);box-shadow:0 4px 18px rgba(0,0,0,.12);text-align:center}
.plan-price{color:var(--brand);font-weight:400}
.plan-price sup{font-size:.4em;vertical-align:top;position:relative;top:.35em}
.plan-price small{font-size:.36em}
.plan-label{font-size:14px;color:#444;text-transform:uppercase}
.plan-small{width:196px;height:196px}
.plan-small .plan-price{margin-top:44px;font-size:33px}
.plan-small .plan-label{margin:16px auto 0;width:110px;padding-top:10px;border-top:1px solid #eee;padding-bottom:10px;border-bottom:1px solid #eee}
.plan-main{left:411px;top:1632px;width:380px;height:380px}
.plan-main .plan-price{margin-top:56px;font-size:55px}
.plan-main .plan-label{margin:14px auto 0;width:176px;padding:8px 0;border-top:1px solid #eee;border-bottom:1px solid #eee}
.plan-main p{margin:14px auto 0;width:260px;font-size:13.4px;line-height:19px;color:var(--muted)}
.know-btn{margin:18px auto 0;width:152px;height:38px}
.plan-arrow{top:1814px;width:20px;height:16px}

/* advice */
.advice-title{left:74px;top:2110px;font-size:31px;font-weight:400;color:#222}
.advice-sub{left:74px;top:2146px;font-size:19px;font-weight:400;color:#333;text-transform:uppercase}
.advice-card{left:74px;top:2188px;width:691px;height:282px;background:var(--pale)}
.advice-text{left:102px;top:2219px;width:470px;font-size:13px;line-height:22px;color:#444}
.stars{left:102px;top:2371px;font-size:16px;color:var(--star);letter-spacing:1px}
.review-meta{left:102px;top:2395px;font-size:14px;line-height:21px;color:#333}
.advice-portrait{left:570px;top:2188px;width:190px;height:282px;background:linear-gradient(180deg,var(--pale) 0%,#c7a07c 40%,#9b6a43 100%)}

.contact-card{left:808px;top:2114px;width:318px;height:356px;background:var(--pale)}
.contact-title{left:832px;top:2139px;font-size:20px;font-weight:400;color:#222;text-transform:uppercase}
.field{left:832px;width:268px;height:34px;background:var(--white);border:1px solid #dde3e7;border-radius:3px;font-size:12px;color:#999;padding:10px 14px}
.field svg{position:absolute;right:12px;top:10px;width:14px;height:14px}
.submit{left:832px;top:2413px;width:268px;height:36px;border-radius:3px}

/* footer */
.site-footer{left:0;top:2522px;width:1200px;height:68px;background:var(--footer)}
.copyright{left:74px;top:2549px;font-size:13px;color:#d0d0d0}
.social{top:2543px;width:28px;height:28px;border:2px solid #d0d0d0;border-radius:50%}
</style>
</head>
<body>

<header>
  <div class="abs top-bar"></div>
  <div class="abs quick-phone">
    <svg viewBox="0 0 26 26"><circle cx="13" cy="13" r="12" fill="none" stroke="#fff" stroke-width="1.5"/><path d="M9.5 7.5l2 2.6-1.2 1.4c.8 1.7 2 2.9 3.7 3.7l1.4-1.2 2.6 2-1.3 2.2c-4.6-.4-8.8-4.6-9.2-9.2z" fill="#fff"/></svg>
    <span>Quick Contact - <strong>(206) 555-0148</strong></span>
  </div>
  <div class="abs nav-bar"></div>
  <div class="abs brand-badge"><span class="brand-name">Kestrel<br>Way</span></div>
  <nav class="abs main-nav">
    <span class="active-dot"></span>
    <a class="active" style="left:586px">Home</a>
    <a style="left:679px">About Us</a>
    <a style="left:777px">Services</a>
    <a style="left:889px">Testimonials</a>
    <a style="left:991px">News</a>
    <a style="left:1088px">Contact Us</a>
  </nav>
</header>

<section>
  <div class="abs hero" role="img" aria-label="Seattle skyline at dusk with the tower and downtown lights"></div>
  <h1 class="abs hero-title" style="top:346px">Kestrel Way is a Seattle based<br>mobile massage service</h1>
  <svg class="abs hero-arrow" style="left:72px;top:379px" viewBox="0 0 24 30"><path d="M18 3L6 15l12 12" fill="none" stroke="#fff" stroke-width="4"/></svg>
  <svg class="abs hero-arrow" style="left:1105px;top:379px" viewBox="0 0 24 30"><path d="M6 3l12 12L6 27" fill="none" stroke="#fff" stroke-width="4"/></svg>
</section>

<section>
  <h2 class="abs section-title why-title">Why we stand out?</h2>
  <p class="abs why-text">We are a male and female mobile massage team. Our names are Paul and Lina. Kestrel Way is a Seattle based mobile massage service. Our massage is offered to the community with a goal of facilitating balance within each individual. We specialize in integrated Pain management, and sports/medical massage therapy. Every client's first assessment is attended by our male and female massage therapist team. Depending on the goals identified for an individual determines which therapist will be assigned to provide treatment, if not both.</p>
  <div class="abs btn learn-btn">Learn More</div>
  <div class="abs why-media" role="img" aria-label="Client relaxing during a back massage with oil and lilies"></div>
  <svg class="abs play" viewBox="0 0 64 64"><circle cx="32" cy="32" r="29" fill="rgba(255,255,255,.2)" stroke="#fff" stroke-width="3"/><path d="M26 20l18 12-18 12z" fill="#fff"/></svg>
</section>

<section>
  <div class="abs passion"></div>
  <h2 class="abs passion-title">OUR PASSION</h2>
  <p class="abs passion-text">Here at Kestrel Way, we have a great passion for Postural Resoration and how it isintegrated into an individual's Massage treatment. We pride ourselves in being natural facilitators of healing, which takes the ego of the therapist out of the client's healing process. We strive to deliver the best massage possible by including modalities such as Neuromuscular, Myofascial release, spontaneous muscle release, postural restoration, orthopedic, and medical massage.</p>
  <div class="abs feature" style="left:80px;top:1240px">
    <svg class="feature-icon" viewBox="0 0 110 110" role="img" aria-label="Healing hand icon"><circle cx="55" cy="55" r="52" fill="none" stroke="#05a7d8" stroke-width="3"/><circle cx="55" cy="55" r="45" fill="#05a7d8"/></svg>
    <h3>Dolore Dipus</h3>
    <p>Lorem ipsum dolor sit amet, ectetur adipisc<br>elit nullam eget Lorem ipsum sit.</p>
  </div>
  <div class="abs feature" style="left:439px;top:1240px">
    <svg class="feature-icon" viewBox="0 0 110 110" role="img" aria-label="Massage treatment icon"><circle cx="55" cy="55" r="52" fill="none" stroke="#05a7d8" stroke-width="3"/><circle cx="55" cy="55" r="45" fill="#05a7d8"/></svg>
    <h3>Dolore Dipus</h3>
    <p>Lorem ipsum dolor sit amet, ectetur adipisc<br>elit nullam eget Lorem ipsum sit.</p>
  </div>
  <div class="abs feature" style="left:800px;top:1240px">
    <svg class="feature-icon" viewBox="0 0 110 110" role="img" aria-label="Yoga pose icon"><circle cx="55" cy="55" r="52" fill="none" stroke="#05a7d8" stroke-width="3"/><circle cx="55" cy="55" r="45" fill="#05a7d8"/></svg>
    <h3>Dolore Dipus</h3>
    <p>Lorem ipsum dolor sit amet, ectetur adipisc<br>elit nullam eget Lorem ipsum sit.</p>
  </div>
</section>

<section>
  <div class="abs pricing-band"></div>
  <div class="abs pricing-base"></div>
  <p class="abs pricing-kicker">Our Packages &amp;</p>
  <h2 class="abs pricing-title">Pricing Plans</h2>
  <div class="abs plan plan-small" style="left:206px;top:1724px">
    <div class="plan-price"><sup>$</sup>75 <small>/60 MO</small></div>
    <div class="plan-label">Dolor sit elit</div>
  </div>
  <div class="abs plan plan-small" style="left:814px;top:1724px">
    <div class="plan-price"><sup>$</sup>120 <small>/120 MO</small></div>
    <div class="plan-label">Dolor sit elit</div>
  </div>
  <svg class="abs plan-arrow" style="left:434px" viewBox="0 0 20 16"><path d="M19 8H2M8 2L2 8l6 6" fill="none" stroke="#888" stroke-width="1.5"/></svg>
  <svg class="abs plan-arrow" style="left:750px" viewBox="0 0 20 16"><path d="M1 8h17M12 2l6 6-6 6" fill="none" stroke="#888" stroke-width="1.5"/></svg>
  <div class="abs plan plan-main">
    <div class="plan-price"><sup>$</sup>95 <small>/90 MO</small></div>
    <div class="plan-label">Dolor sit elit eget</div>
    <p>Lorem ipsum dolor sit amet, ectetur adipisc elit nullam eget</p>
    <div class="btn know-btn">Know More</div>
  </div>
</section>

<section>
  <h2 class="abs advice-title">ADVICE</h2>
  <p class="abs advice-sub">To any massage client</p>
  <div class="abs advice-card"></div>
  <p class="abs advice-text">The most important thing to 'us', as Licenced providers is to get you on to our table to show you our skills. But a good therapist never forgets that it's not about what we do for you, but what we can facilitate for you. Your health and healing has nothing to do with us. It is yours, not ours. Identify what your goals are with any Therapist, and know what the end looks like. Progress should be tangible, such as range of motion, and decreased pain.</p>
  <div class="abs stars">★★★★★</div>
  <p class="abs review-meta">5/5 stars Massage Therapy<br>Verified Review</p>
  <div class="abs advice-portrait" role="img" aria-label="Portrait of a smiling reviewer in a brown jacket"></div>

  <div class="abs contact-card"></div>
  <h2 class="abs contact-title">Quick Contact</h2>
  <div class="abs field" style="top:2180px">Enter Name<svg viewBox="0 0 14 14"><circle cx="7" cy="4" r="3" fill="#888"/><path d="M1 13c0-3.5 2.7-5.5 6-5.5s6 2 6 5.5z" fill="#888"/></svg></div>
  <div class="abs field" style="top:2228px">Enter Email<svg viewBox="0 0 14 14"><rect x="1" y="3" width="12" height="9" fill="#888"/><path d="M1 3l6 5 6-5" fill="none" stroke="#fff" stroke-width="1.2"/></svg></div>
  <div class="abs field" style="top:2276px">Enter Phone<svg viewBox="0 0 14 14"><path d="M2.5 1.5l2.5 3-1.3 1.6c1 2 2.2 3.2 4.2 4.2l1.6-1.3 3 2.5-1.5 2C5.8 13 1 8.2.5 3z" fill="#888"/></svg></div>
  <div class="abs field" style="top:2326px;height:71px">Leave Message<svg viewBox="0 0 14 14"><path d="M7 2C3.7 2 1 4 1 6.5c0 1.4.8 2.6 2 3.4L2.5 12.5 5.5 11c.5.1 1 .1 1.5.1 3.3 0 6-2 6-4.6S10.3 2 7 2z" fill="none" stroke="#888" stroke-width="1.2"/></svg></div>
  <div class="abs btn submit">Submit Here</div>
</section>

<footer>
  <div class="abs site-footer"></div>
  <p class="abs copyright">Copyright © 2015 Yoursitename. All rights reserved.</p>
  <span class="abs social" style="left:977px"></span>
  <span class="abs social" style="left:1015px"></span>
  <span class="abs social" style="left:1055px"></span>
  <span class="abs social" style="left:1093px"></span>
</footer>

</body>
</html>
```